Business Card Design - Photographer

I am a landscape photographer and I require a business card design. 

I require two designs:
1)  a double sided business card
 and
b)  a single sided business card 

The single sided design can either be the same as the double sided (with just one side having all the information)....or it can be an entire new design. Its up to you.

My corporate colours are (CMYK):

Blue   69, 32, 0, 0
Grey  72,  64,  47,  31
Green  32,  2,  91,  0
Yellow   0, 19, 92, 0
Orange  0, 39, 75, 0

Colour space in final file should be in CMYK.

The details that need to be included on the card:

- Use the provided Logo
- Name: Wiktor Baranowski
- Email:   sales@vistalumeworks.com.au
- Website:    vistalumeworks.com.au
- Twitter:    twitter.com/vistalumeworks
- Facebook:   facebook.com/vistalumeworks
- Mobile  0417 539 662

Please use the attached template to design the logo to the specified size, including the marked bleed lines. I have also attached my logo in PNG (transparent background) and ai format for you to use.

The final file should be:
- Photoshop version with layers so I can edit the name/text etc. All non vector files should be high resolution at 1039 x 697 pixels at 300 dpi.

I also require a file as:
- Vector based PDF

Anyway questions please contact me.

Thank you

Industry/Entity Type

Landscape

Logo styles of interest
Pictorial/Combination Logo
Abstract Logo
Wordmark Logo
Lettermark Logo
Requirements
Must have
• The details that need to be included on the card:

- Use the provided Logo
- Name: Wiktor Baranowski
- Email: sales@vistalumeworks.com.au
- Website: vistalumeworks.com.au
- Twitter: twitter.com/vistalumeworks
- Facebook: facebook.com/vistalumeworks
- Mobile 0417 539 662

```html
<!DOCTYPE html>
<html lang="en">
<head>
<meta charset="utf-8">
<title>Vista Lume Works – Business Card</title>
<link rel="stylesheet" href="https://fonts.googleapis.com/css2?family=Cinzel:wght@500;600;700&family=Tinos&display=swap">
<style>
  :root {
    --backdrop: #ecebe8;
    --card: #ffffff;
    --card-edge: #5a4a3e;
    --ink: #363a4c;
    --slate: #868890;
    --brand-blue: #7fb0dc;
    --brand-grey: #5c6170;
    --brand-green: #bcd56e;
    --brand-yellow: #f7d047;
    --brand-orange: #f8bc86;
  }
  * { margin: 0; padding: 0; box-sizing: border-box; }
  html, body { width: 1200px; height: 374px; overflow: hidden; }
  body { position: relative; background: var(--backdrop); color: var(--ink); font-family: "Tinos", "Times New Roman", serif; }

  .card {
    position: absolute; top: 37px; width: 526px; height: 299px;
    background: var(--card); border: 1px solid var(--card-edge);
    border-radius: 14px; overflow: hidden;
  }
  .card--back { left: 45px; }
  .card--front { left: 601px; }

  .brand-name {
    font-family: "Cinzel", "Trajan Pro", serif; font-weight: 600;
    color: var(--ink); white-space: nowrap; text-align: center;
  }
  .brand-rule { height: 1px; background: var(--ink); }
  .brand-tagline {
    font-family: "Cinzel", "Trajan Pro", serif; font-weight: 700; color: var(--ink);
    white-space: nowrap; text-align: center;
  }

  /* back card */
  .logo-disc {
    position: absolute; left: 107px; top: 16px; width: 76px; height: 76px;
    border-radius: 50%; background: var(--brand-grey);
  }
  .card--back .brand-block { position: absolute; left: 40px; top: 102px; width: 210px; }
  .card--back .brand-name { font-size: 20px; letter-spacing: 0.2px; }
  .card--back .brand-rule { margin-top: 2px; }
  .card--back .brand-tagline { font-size: 9px; letter-spacing: 1.5px; margin-top: 3px; }

  .contact-list { position: absolute; left: 40px; top: 161px; list-style: none; }
  .contact-list li { display: flex; align-items: center; height: 18.7px; font-size: 13px; }
  .contact-icon { width: 10px; height: 10px; margin-right: 5px; fill: var(--ink); flex: none; }
  .social-mark { width: 9px; height: 9px; margin-right: 6px; background: var(--brand-blue); border-radius: 1px; flex: none; }
  .social-mark--alt { background: var(--brand-grey); }
  .address { position: absolute; left: 40px; top: 268px; font-size: 13px; }

  .accent-disc {
    position: absolute; left: 407px; top: 28px; width: 240px; height: 250px;
    border-radius: 50%; background: var(--slate);
  }

  /* front card */
  .leaf-motif {
    position: absolute; left: 0; top: 28px; width: 122px; height: 248px;
    border-radius: 0 60px 60px 0;
    background:
      radial-gradient(circle at 30% 18%, var(--brand-orange) 0 14%, transparent 30%),
      radial-gradient(circle at 75% 30%, var(--brand-green) 0 12%, transparent 28%),
      radial-gradient(circle at 25% 45%, var(--brand-blue) 0 14%, transparent 30%),
      radial-gradient(circle at 80% 55%, var(--brand-yellow) 0 12%, transparent 28%),
      radial-gradient(circle at 45% 75%, var(--brand-orange) 0 12%, transparent 28%),
      radial-gradient(circle at 20% 88%, var(--brand-green) 0 10%, transparent 24%),
      radial-gradient(circle at 60% 90%, var(--brand-blue) 0 10%, transparent 24%),
      linear-gradient(180deg, #f3f5f8, #eef0f3);
  }
  .card--front .brand-block { position: absolute; left: 153px; top: 122px; width: 326px; }
  .card--front .brand-name { font-size: 29.5px; letter-spacing: 0.5px; }
  .card--front .brand-rule { margin-top: 2px; }
  .card--front .brand-tagline { font-size: 12px; letter-spacing: 3.4px; margin-top: 6px; }
  .web-address {
    position: absolute; left: 150px; top: 203px; width: 332px; text-align: center;
    font-size: 12.5px; letter-spacing: 4px; white-space: nowrap;
  }
</style>
</head>
<body>
  <section class="card card--back">
    <div class="logo-disc"></div>
    <div class="brand-block">
      <div class="brand-name">VISTA LUME WORKS</div>
      <div class="brand-rule"></div>
      <div class="brand-tagline">FINE ART PHOTOGRAPHY</div>
    </div>

    <ul class="contact-list">
      <li>
        <svg class="contact-icon" viewBox="0 0 10 10"><rect x="2.5" y="0.5" width="5" height="9" rx="1"/><rect x="3.5" y="1.8" width="3" height="4.5" fill="#fff"/></svg>
        0417 539 662
      </li>
      <li>
        <svg class="contact-icon" viewBox="0 0 10 10"><rect x="0.5" y="2" width="9" height="6.5"/><path d="M0.8 2.4 5 5.6 9.2 2.4" stroke="#fff" stroke-width="0.8" fill="none"/></svg>
        sales@vistalumeworks.com.au
      </li>
      <li>
        <svg class="contact-icon" viewBox="0 0 10 10"><circle cx="5" cy="5" r="4.3"/></svg>
        www.vistalumeworks.com.au
      </li>
      <li><span class="social-mark"></span>vistalumeworks</li>
      <li><span class="social-mark social-mark--alt"></span>vistalumeworks</li>
    </ul>

    <p class="address">00, Complex Name, State Name, City 0020</p>

    <div class="accent-disc"></div>
  </section>

  <section class="card card--front">
    <div class="leaf-motif" role="img" aria-label="Decorative leaf motif in brand blue, green, yellow, orange and grey"></div>
    <div class="brand-block">
      <div class="brand-name">VISTA LUME WORKS</div>
      <div class="brand-rule"></div>
      <div class="brand-tagline">FINE ART PHOTOGRAPHY</div>
    </div>
    <p class="web-address">www.vistalumeworks.com.au</p>
  </section>
</body>
</html>
```